Business Card Design

We need the business card for our new business based in St. Marys, we manufacture mainly bubble wraps. And we would like the design to use our company logo and also make it easy for people to understand right away we are bubble wrap manufacturer

Industry/Entity Type

Business

Contact Information for Business Card

Cushtane Pty Ltd, 14 Larkin Road Kelverton NSW 2794, Tel: 02 9471 5826, Fax: 9471 5839, Dara Oyelaran, General Manager, Mobile :0438 217 564, dara.oyelaran@cushtane.com.au, Website: cushtane.com.au

```html
<!DOCTYPE html>
<html lang="en">
<head>
<meta charset="utf-8">
<title>Cushtane Pty Ltd — Business Card</title>
<link href="https://fonts.googleapis.com/css2?family=Arimo:wght@400;700&family=Montserrat:wght@500;800&display=swap" rel="stylesheet">
<style>
  :root {
    --red: #b5121b;
    --red-dark: #8e0d14;
    --grey: #6f6b74;
    --grey-dark: #4e4a52;
    --ink: #4a474d;
    --paper: #f7f9f9;
    --backdrop: #3b3c40;
    --white: #ffffff;
  }
  * { margin: 0; padding: 0; box-sizing: border-box; }
  html, body { width: 1200px; height: 960px; overflow: hidden; }
  body {
    background: var(--backdrop);
    font-family: "Arimo", Arial, sans-serif;
    display: flex;
    flex-direction: column;
    align-items: center;
    justify-content: center;
    gap: 40px;
  }
  .card {
    position: relative;
    width: 680px;
    height: 416px;
    background: var(--paper);
    overflow: hidden;
    box-shadow: 0 10px 30px rgba(0,0,0,.35);
  }
  .card-shapes { position: absolute; inset: 0; }
  .brand { position: absolute; text-align: left; }
  .brand-name {
    font-family: "Montserrat", sans-serif;
    font-weight: 800;
    font-size: 54px;
    letter-spacing: 1px;
    color: var(--ink);
    line-height: 1;
  }
  .brand-tagline {
    font-family: "Montserrat", sans-serif;
    font-weight: 500;
    font-size: 11px;
    letter-spacing: 4.2px;
    color: var(--grey);
    margin-top: 8px;
    white-space: nowrap;
  }
  .card-front .brand { left: 170px; top: 150px; }
  .website {
    position: absolute;
    right: 40px;
    bottom: 52px;
    color: var(--white);
    font-size: 17px;
  }
  .card-back .brand { right: 40px; top: 50px; }
  .card-back .brand-name { font-size: 44px; }
  .card-back .brand-tagline { font-size: 9px; letter-spacing: 3.4px; }
  .person-name {
    position: absolute;
    left: 26px; top: 126px;
    color: var(--white);
    font-size: 26px;
    font-weight: 700;
    white-space: nowrap;
  }
  .person-title {
    position: absolute;
    left: 56px; top: 168px;
    color: var(--white);
    font-size: 16px;
    white-space: nowrap;
  }
  .contacts {
    position: absolute;
    display: grid;
    gap: 12px;
    color: var(--white);
    font-size: 15px;
  }
  .contacts li { list-style: none; display: flex; align-items: center; gap: 10px; white-space: nowrap; }
  .contacts svg { width: 22px; height: 22px; flex: none; }
  .contacts-main { left: 40px; top: 262px; }
  .contacts-side { left: 400px; top: 296px; }
</style>
</head>
<body>

  <section class="card card-front">
    <svg class="card-shapes" viewBox="0 0 680 416" aria-hidden="true">
      <rect x="0" y="0" width="680" height="26" fill="var(--red)"/>
      <polygon points="0,372 318,372 342,344 342,416 0,416" fill="var(--grey)"/>
      <polygon points="440,282 478,240 680,240 680,282" fill="var(--grey)"/>
      <polygon points="356,416 356,334 398,290 680,290 680,416" fill="var(--red)"/>
      <line x1="398" y1="290" x2="680" y2="290" stroke="var(--white)" stroke-width="3"/>
    </svg>
    <div class="brand">
      <div class="brand-name">CUSHTANE</div>
      <div class="brand-tagline">PROTECTIVE PACKAGING SOLUTIONS</div>
    </div>
    <div class="website">www.cushtane.com.au</div>
  </section>

  <section class="card card-back">
    <svg class="card-shapes" viewBox="0 0 680 416" aria-hidden="true">
      <line x1="0" y1="222" x2="680" y2="222" stroke="var(--grey-dark)" stroke-width="1.5"/>
      <rect x="0" y="230" width="680" height="186" fill="var(--red)"/>
      <line x1="0" y1="236" x2="680" y2="236" stroke="var(--white)" stroke-width="1.5"/>
      <polygon points="0,118 258,118 240,160 0,160" fill="var(--red)"/>
      <polygon points="36,160 230,160 230,196 36,196" fill="var(--grey)"/>
      <polygon points="230,160 244,140 244,182 230,196" fill="var(--grey-dark)"/>
    </svg>
    <div class="brand">
      <div class="brand-name">CUSHTANE</div>
      <div class="brand-tagline">PROTECTIVE PACKAGING SOLUTIONS</div>
    </div>
    <div class="person-name">Dara Oyelaran</div>
    <div class="person-title">General Manager</div>

    <ul class="contacts contacts-main">
      <li>
        <svg viewBox="0 0 22 22"><rect width="22" height="22" rx="4" fill="#fff"/><path d="M11 4a5 5 0 0 0-5 5c0 4 5 9 5 9s5-5 5-9a5 5 0 0 0-5-5zm0 7a2 2 0 1 1 0-4 2 2 0 0 1 0 4z" fill="var(--red)"/></svg>
        Cushtane Pty Ltd, 14 Larkin Road Kelverton NSW 2794
      </li>
      <li>
        <svg viewBox="0 0 22 22"><rect width="22" height="22" rx="4" fill="#fff"/><path d="M7 4l3 3-1.5 2a9 9 0 0 0 4.5 4.5L15 12l3 3-2 2.5C10 17 5 12 4.5 6z" fill="var(--red-dark)"/></svg>
        02 9471 5826
      </li>
      <li>
        <svg viewBox="0 0 22 22"><rect width="22" height="22" rx="4" fill="#fff"/><rect x="7" y="4" width="8" height="14" rx="1.5" fill="none" stroke="var(--red-dark)" stroke-width="1.6"/><circle cx="11" cy="15.5" r="1" fill="var(--red-dark)"/></svg>
        0438 217 564
      </li>
    </ul>

    <ul class="contacts contacts-side">
      <li>
        <svg viewBox="0 0 22 22"><rect width="22" height="22" rx="4" fill="#fff"/><rect x="7" y="4" width="8" height="5" fill="var(--red-dark)"/><rect x="4" y="9" width="14" height="6" rx="1" fill="var(--red-dark)"/><rect x="7" y="13" width="8" height="5" fill="#fff" stroke="var(--red-dark)" stroke-width="1.2"/></svg>
        9471 5839
      </li>
      <li>
        <svg viewBox="0 0 22 22"><rect width="22" height="22" rx="4" fill="#fff"/><rect x="4" y="6" width="14" height="10" rx="1" fill="var(--red-dark)"/><path d="M4.5 6.5L11 12l6.5-5.5" fill="none" stroke="#fff" stroke-width="1.4"/></svg>
        dara.oyelaran@cushtane.com.au
      </li>
    </ul>
  </section>

</body>
</html>
```